Ward Compass Business Card Design*

We need a business card design for our company Ward Compass. Our company is specialized in providing online consulting services regarding medical institutions, hospitals and doctors. We work with patients worldwide looking to choose between healthcare providers. We have a website you may use as a reference, where we list doctors and clinics worldwide. So we target Medical providers as well as patients worldwide.
Target Market(s)
Medical Providers and patients around the world
Industry/Entity Type
Medical
Contact Information for Business Card
Salwa Kettani
CEO
+90 612 348 2175
info@wardcompass.example
www.wardcompass.example
14 Annakhil 7 H.R.B. Rabat, Morocco
Requirements
Must have
- Company logo/name on one full side, personal info and smaller logo and company name on the other side.
Nice to have
- Smart and elegant design

```html
<!DOCTYPE html>
<html lang="en">
<head>
<meta charset="utf-8">
<title>Ward Compass – Business Card</title>
<link rel="stylesheet" href="https://fonts.googleapis.com/css2?family=Montserrat:wght@400;600;700&display=swap">
<style>
  :root {
    --stage: #e9e6e1;
    --navy: #134b86;
    --navy-deep: #0d3a6b;
    --navy-light: #1d5b9a;
    --paper: #ffffff;
    --paper-shade: #eceef0;
    --silver: #a9adb2;
    --ink-light: #ffffff;
    --brand-ink: #1a4c86;
  }
  * { box-sizing: border-box; margin: 0; padding: 0; }
  html, body { width: 1200px; height: 780px; overflow: hidden; }
  body {
    background: var(--stage);
    font-family: "Montserrat", sans-serif;
    display: flex;
    align-items: center;
    justify-content: center;
    gap: 40px;
  }
  .card {
    position: relative;
    width: 540px;
    height: 309px;
    border-radius: 4px;
    overflow: hidden;
    box-shadow: 0 10px 28px rgba(0,0,0,.18);
  }
  .card-art { position: absolute; inset: 0; width: 100%; height: 100%; }

  /* front side */
  .front-brand {
    position: absolute;
    left: 138px; top: 62px;
    display: flex; align-items: center; gap: 10px;
    color: var(--brand-ink);
  }
  .brand-dot {
    width: 30px; height: 30px; border-radius: 50%;
    background: var(--brand-ink);
  }
  .brand-name {
    font-weight: 600;
    font-size: 17px;
    letter-spacing: 1.5px;
    text-transform: uppercase;
  }
  .social-links {
    position: absolute; right: 28px; top: 96px;
    display: flex; gap: 7px;
  }
  .social-links span {
    width: 16px; height: 16px; border-radius: 3px;
    background: var(--paper-shade);
    opacity: .9;
  }
  .person {
    position: absolute; left: 34px; top: 176px;
    color: var(--ink-light);
  }
  .person-name {
    font-size: 16px; font-weight: 600;
    letter-spacing: .5px; text-transform: uppercase;
  }
  .person-role { font-size: 11px; font-weight: 400; letter-spacing: 1px; opacity: .85; margin-top: 2px; }
  .contact-list {
    position: absolute; left: 34px; bottom: 26px;
    list-style: none; color: var(--ink-light);
    font-size: 10.5px; line-height: 1;
  }
  .contact-list li { display: flex; align-items: center; gap: 8px; margin-top: 6px; }
  .contact-list svg { width: 13px; height: 13px; flex: none; }

  /* back side */
  .back-brand {
    position: absolute; inset: 0;
    display: flex; align-items: center; justify-content: center; gap: 14px;
    color: var(--ink-light);
  }
  .back-brand .brand-dot { width: 40px; height: 40px; background: var(--paper-shade); }
  .back-brand .brand-name { font-size: 24px; letter-spacing: 2.5px; }
</style>
</head>
<body>

  <section class="card card-front" aria-label="Business card, front side">
    <svg class="card-art" viewBox="0 0 540 309" aria-hidden="true">
      <defs>
        <linearGradient id="frontBlue" x1="0" y1="0" x2="1" y2="1">
          <stop offset="0" stop-color="#1a5797"/>
          <stop offset="1" stop-color="#0e3d70"/>
        </linearGradient>
      </defs>
      <rect width="540" height="309" fill="var(--paper)"/>
      <path d="M0 168 C120 172 210 150 300 92 C360 52 420 30 540 24 L540 309 L0 309 Z" fill="var(--silver)"/>
      <path d="M0 180 C125 184 215 160 305 102 C365 62 425 40 540 34 L540 309 L0 309 Z" fill="url(#frontBlue)"/>
      <circle cx="95" cy="235" r="92" fill="#ffffff" opacity=".05"/>
    </svg>

    <div class="front-brand">
      <span class="brand-dot"></span>
      <span class="brand-name">Ward Compass</span>
    </div>

    <div class="social-links" aria-hidden="true"><span></span><span></span><span></span></div>

    <div class="person">
      <p class="person-name">Salwa Kettani</p>
      <p class="person-role">CEO</p>
    </div>

    <ul class="contact-list">
      <li>
        <svg viewBox="0 0 14 14" aria-hidden="true"><circle cx="7" cy="7" r="7" fill="#fff"/><path d="M4.6 3.6l1.3 1.5-.7.9c.5 1 1.3 1.8 2.3 2.3l.9-.7 1.5 1.3-.8 1.1C6.4 9.8 4.2 7.6 3.6 4.4z" fill="var(--navy)"/></svg>
        <span>+90 612 348 2175</span>
      </li>
      <li>
        <svg viewBox="0 0 14 14" aria-hidden="true"><circle cx="7" cy="7" r="7" fill="#fff"/><rect x="3.6" y="4.6" width="6.8" height="4.8" fill="none" stroke="var(--navy)" stroke-width="1"/><path d="M3.6 4.6L7 7.3l3.4-2.7" fill="none" stroke="var(--navy)" stroke-width="1"/></svg>
        <span>info@wardcompass.example</span>
      </li>
      <li>
        <svg viewBox="0 0 14 14" aria-hidden="true"><circle cx="7" cy="7" r="7" fill="#fff"/><circle cx="7" cy="7" r="3.6" fill="none" stroke="var(--navy)" stroke-width=".9"/><ellipse cx="7" cy="7" rx="1.5" ry="3.6" fill="none" stroke="var(--navy)" stroke-width=".9"/><path d="M3.4 7h7.2" stroke="var(--navy)" stroke-width=".9"/></svg>
        <span>www.wardcompass.example</span>
      </li>
    </ul>
  </section>

  <section class="card card-back" aria-label="Business card, back side">
    <svg class="card-art" viewBox="0 0 540 309" aria-hidden="true">
      <defs>
        <radialGradient id="backBlue" cx=".45" cy=".4" r=".8">
          <stop offset="0" stop-color="#1d5b9a"/>
          <stop offset="1" stop-color="#0d3a6b"/>
        </radialGradient>
      </defs>
      <rect width="540" height="309" fill="url(#backBlue)"/>
      <circle cx="190" cy="150" r="120" fill="#ffffff" opacity=".05"/>
    </svg>
    <div class="back-brand">
      <span class="brand-dot"></span>
      <span class="brand-name">Ward Compass</span>
    </div>
  </section>

</body>
</html>
```